business card stylish and chique

I'd like to have a new business card. I am a certified pilates instructor. my website is www.bloomcorestudio-example.com. Next to teaching pilates in napa valley and around the globe, I offer luxury wellness travel in Napa Valley. (plus I make art and healthy food. my instagram is @lra_vmkt)
I'd love to have an eye catching (bold and unique) card that says in gold or embossed LRA VMKT . (but open for any creative idea)
The back should have my info:
LauraVemkot@mailbox-example.com.
I love whimsical and think the murals at the Orvell hotel in Miami and the Brambi prints are my dreamworld. I'd love on the back my email address and the whimsical design.

Target Market(s)

see description

Industry/Entity Type

Health And Wellness

Contact Information for Business Card

see above

Colors

Designer to choose colors to be used in the design.

Requirements
Must have
• multicolor on back, whimsical print (allowed to use, pref own design)
• probably just white (or black or other single color with LRA VMKT standing out
Nice to have
• open
Should not have
• crazy fonts

```html
<!DOCTYPE html>
<html lang="en">
<head>
<meta charset="UTF-8">
<title>Laura Vemkot – Business Card</title>
<link rel="stylesheet" href="https://fonts.googleapis.com/css2?family=Bebas+Neue&family=Open+Sans:wght@400;600&display=swap">
<style>
  :root {
    --page-bg: #2a2b2e;
    --card-black: #1c1c1e;
    --emboss-dark: #141415;
    --emboss-light: rgba(255,255,255,0.09);
    --sky-light: #f4f1ea;
    --sky-gold: #f0a526;
    --hills: #4a4f45;
    --field: #5a6b3a;
    --grass: #6fa52a;
    --grass-deep: #3f6a1c;
    --band: rgba(40,40,40,0.55);
    --text-light: #ffffff;
  }
  * { margin: 0; padding: 0; box-sizing: border-box; }
  html, body { width: 1200px; height: 900px; overflow: hidden; }
  body { background: var(--page-bg); position: relative; }

  .card {
    position: absolute;
    left: 250px;
    width: 700px;
    height: 400px;
    overflow: hidden;
    box-shadow: 0 12px 30px rgba(0,0,0,0.45);
  }
  .card--front { top: 40px; background: var(--card-black); }
  .card--back { top: 460px; }

  .monogram {
    position: absolute;
    inset: 0;
    display: flex;
    align-items: center;
    justify-content: center;
    font-family: "Bebas Neue", sans-serif;
    font-size: 118px;
    letter-spacing: 2px;
    color: var(--emboss-dark);
    text-shadow: -1px -1px 1px rgba(0,0,0,0.8), 2px 2px 1px var(--emboss-light);
  }

  .landscape {
    position: absolute;
    inset: 0;
    background: linear-gradient(180deg,
      var(--sky-light) 0%,
      #f3d9a4 14%,
      var(--sky-gold) 26%,
      var(--hills) 30%,
      var(--field) 50%,
      var(--grass) 68%,
      var(--grass-deep) 100%);
  }
  .info-band {
    position: absolute;
    left: 0; right: 0;
    top: 120px;
    height: 160px;
    background: var(--band);
  }
  .identity {
    position: absolute;
    top: 150px;
    left: 44px;
    display: flex;
    align-items: center;
    gap: 20px;
  }
  .name {
    font-family: "Bebas Neue", sans-serif;
    font-size: 58px;
    line-height: 1;
    color: var(--text-light);
    letter-spacing: 0.5px;
  }
  .divider { width: 1.5px; height: 82px; background: var(--text-light); }
  .contacts { list-style: none; }
  .contact {
    display: flex;
    align-items: center;
    gap: 9px;
    font-family: "Open Sans", sans-serif;
    font-size: 16.5px;
    line-height: 26px;
    color: var(--text-light);
  }
  .contact svg { width: 15px; height: 15px; flex: none; }
</style>
</head>
<body>
  <section class="card card--front">
    <div class="monogram">LRA VMKT</div>
  </section>

  <section class="card card--back">
    <div class="landscape" role="img" aria-label="Photograph of a vineyard landscape at sunset with golden sky, rolling hills and green grass"></div>
    <div class="info-band"></div>
    <div class="identity">
      <h1 class="name">Laura Vemkot</h1>
      <span class="divider"></span>
      <ul class="contacts">
        <li class="contact">
          <svg viewBox="0 0 16 16"><circle cx="8" cy="8" r="6" fill="none" stroke="#fff" stroke-width="1.6"/></svg>
          @lra_vmkt
        </li>
        <li class="contact">
          <svg viewBox="0 0 16 16"><rect x="1.5" y="3.5" width="13" height="9" fill="none" stroke="#fff" stroke-width="1.4"/><path d="M1.5 3.5 8 9l6.5-5.5" fill="none" stroke="#fff" stroke-width="1.4"/></svg>
          LauraVemkot@mailbox-example.com
        </li>
        <li class="contact">
          <svg viewBox="0 0 16 16"><circle cx="8" cy="8" r="6.3" fill="none" stroke="#fff" stroke-width="1.3"/><ellipse cx="8" cy="8" rx="2.8" ry="6.3" fill="none" stroke="#fff" stroke-width="1.1"/><path d="M1.7 8h12.6" stroke="#fff" stroke-width="1.1"/></svg>
          www.bloomcorestudio-example.com
        </li>
      </ul>
    </div>
  </section>
</body>
</html>
```